Business Card: RW Office Partners - Your organised problem solver

Business Name: RW Office Partners
Website: www.rwofficepartners.com.au
Email: marisol@rwofficepartners.com.au
Mobile: 61 482 907 236
Facebook: @rwofficepartners
Instrgram: @rwofficepartners

Brading Colours:
HEX
#986474
#ddccd3
#7a8498
#c9d8e4
#000000
#ffffff

Tag Line: Your organised problem solver

Link to DRAFT website:
https://deskhelpcollective.wixsite.com/rw-office-partners

About Page from the website:
My name is Marisol Wrenfield, and I would love to assist you to become more productive in your day to day and achieve your business and personal goals.
My mission is to give you time, time to work on the important tasks of your business or to be able to spend more time with your family. I will take on the tasks you don’t have time for, don’t know well or simply don’t like to do.
I have an extensive background in Administration, Tender Coordination, Document Control, WHS and Quality Management working primarily in the Construction, Mining and Corporate World.
I am passionate about being organised, having order and making things in your life (and mine) easier! I love to watch something unfold and grow into something amazing! I am known for being the go-to problem solver, the organiser of all things, producing high standards of work even under pressure. I’m also a confident communicator, and I understand that you’re busy running your business.

Target Market(s)

Small to Medium Business who require assistance in their business by a virtual assistant.

Industry/Entity Type

Virtual Assistant

Contact Information for Business Card

Mobile: 61 482 907 236

Font styles to use
Sans Serif

Colors
ffffff

Requirements
Must have
• Branding Colours as outlined.
Contact Details as outlined.
Logo as provided.
Proper contact details - mobile, facebook, instragm, website.
Simple, Elegant, very clean looking.
Should not have
• Note cute with pictures.
Not too girly as still want to market to construction companies.

```html
<!DOCTYPE html>
<html lang="en">
<head>
<meta charset="utf-8">
<title>RW Office Partners – Business Card</title>
<link href="https://fonts.googleapis.com/css2?family=Montserrat:wght@500&family=Questrial&display=swap" rel="stylesheet">
<style>
  :root {
    --mauve: #986474;
    --blush: #ddccd3;
    --slate: #7a8498;
    --mist: #c9d8e4;
    --lilac-grey: #b9bccb;
    --black: #000000;
    --white: #ffffff;
    --stage: #ececec;
    --logo-grey: #8e93a8;
  }
  * { margin: 0; padding: 0; box-sizing: border-box; }
  html, body { width: 1200px; height: 796px; overflow: hidden; }
  body {
    background: var(--stage);
    font-family: "Questrial", "Century Gothic", sans-serif;
    display: flex;
    align-items: center;
    justify-content: center;
    gap: 40px;
  }
  .card {
    position: relative;
    width: 520px;
    height: 318px;
    overflow: hidden;
    box-shadow: 0 6px 18px rgba(0,0,0,0.12);
  }

  /* Front */
  .card--front {
    background: var(--black);
    display: flex;
    align-items: center;
    justify-content: center;
  }
  .brand {
    display: flex;
    align-items: center;
    gap: 12px;
  }
  .brand__mark {
    width: 14px;
    height: 14px;
    background: var(--mauve);
  }
  .brand__name {
    font-family: "Montserrat", sans-serif;
    font-weight: 500;
    text-transform: uppercase;
    letter-spacing: 0.06em;
    white-space: nowrap;
  }
  .card--front .brand__name { font-size: 30px; color: var(--logo-grey); }

  /* Back */
  .card--back { background: var(--black); }
  .card__curves { position: absolute; inset: 0; }
  .card--back .brand {
    position: absolute;
    left: 26px;
    top: 192px;
    gap: 10px;
  }
  .card--back .brand__mark { width: 10px; height: 10px; }
  .card--back .brand__name { font-size: 15px; color: var(--mauve); }

  .details {
    position: absolute;
    left: 318px;
    top: 32px;
    width: 190px;
    color: var(--white);
  }
  .details__title {
    font-size: 21px;
    font-weight: 400;
    line-height: 1.1;
    margin-bottom: 22px;
    margin-left: -20px;
    white-space: nowrap;
  }
  .contact-list { list-style: none; }
  .contact-list li {
    display: flex;
    align-items: center;
    gap: 7px;
    font-size: 10.5px;
    line-height: 1;
    margin-bottom: 9px;
    white-space: nowrap;
  }
  .contact-list svg { width: 11px; height: 11px; flex: none; }

  .tagline {
    position: absolute;
    right: 20px;
    bottom: 28px;
    color: var(--white);
    font-size: 9.5px;
    letter-spacing: 0.12em;
    text-align: center;
    white-space: nowrap;
  }
  .tagline::after {
    content: "";
    display: block;
    width: 70px;
    height: 1px;
    background: var(--white);
    margin: 6px auto 0;
  }
</style>
</head>
<body>

  <section class="card card--front" aria-label="Business card front">
    <div class="brand">
      <span class="brand__mark"></span>
      <span class="brand__name">RW Office Partners</span>
    </div>
  </section>

  <section class="card card--back" aria-label="Business card back">
    <svg class="card__curves" viewBox="0 0 520 318" width="520" height="318" aria-hidden="true">
      <rect width="520" height="318" fill="var(--black)"/>
      <circle cx="-120" cy="340" r="424" fill="var(--mauve)"/>
      <circle cx="-120" cy="340" r="416" fill="var(--lilac-grey)"/>
      <circle cx="-120" cy="340" r="410" fill="var(--white)"/>
    </svg>

    <div class="brand">
      <span class="brand__mark"></span>
      <span class="brand__name">RW Office Partners</span>
    </div>

    <div class="details">
      <h1 class="details__title">RW Office Partners</h1>
      <ul class="contact-list">
        <li>
          <svg viewBox="0 0 12 12"><rect x="0.5" y="2" width="11" height="8" fill="var(--blush)"/><path d="M0.5 2 L6 7 L11.5 2" fill="none" stroke="var(--black)" stroke-width="1"/></svg>
          marisol@rwofficepartners.com.au
        </li>
        <li>
          <svg viewBox="0 0 12 12"><circle cx="6" cy="6" r="5.2" fill="none" stroke="var(--blush)" stroke-width="1.2"/><ellipse cx="6" cy="6" rx="2.2" ry="5.2" fill="none" stroke="var(--blush)" stroke-width="1"/><line x1="0.8" y1="6" x2="11.2" y2="6" stroke="var(--blush)" stroke-width="1"/></svg>
          www.rwofficepartners.com.au
        </li>
        <li>
          <svg viewBox="0 0 12 12"><circle cx="6" cy="6" r="5" fill="none" stroke="var(--blush)" stroke-width="1.2"/></svg>
          @rwofficepartners
        </li>
        <li>
          <svg viewBox="0 0 12 12"><rect x="1" y="1" width="10" height="10" fill="var(--blush)"/></svg>
          @rwofficepartners
        </li>
        <li>
          <svg viewBox="0 0 12 12"><path d="M3 1 L5 3.5 L4 5 C4.8 6.6 5.6 7.4 7 8 L8.5 7 L11 9 L9.5 11 C5 10.5 1.5 7 1 2.5 Z" fill="var(--blush)"/></svg>
          61 482 907 236
        </li>
      </ul>
    </div>

    <p class="tagline">Your organised problem solver</p>
  </section>

</body>
</html>
```